Tech business card design

We need an amazing business card design for our new business 'Pexla' a marketing tech startup based in Sydney, Australia. We provide an online marketplace for businesses to search and buy advertising media, connect with service providers and learn more about marketing. We wish to communicate 'cool tech', reliability and professionalism and design based around our logo.

Target Market(s)

Business Owners

Contact Information for Business Card

Name
Position
Email Address
Website
Phone Number

Font styles to use
Other font styles liked:
• Avenir & Avenir Next

Colors

Designer to choose colors to be used in the design.

```html
<!DOCTYPE html>
<html lang="en">
<head>
<meta charset="utf-8">
<title>Pexla Business Card</title>
<link rel="stylesheet" href="https://fonts.googleapis.com/css2?family=Open+Sans:wght@400;700&display=swap">
<style>
  :root {
    --page: #e1dfdf;
    --navy: #22244a;
    --ink: #262630;
    --tab: #d9d9e4;
    --tab-fold: #a3a3b8;
    --back: #d9d9e5;
    --white: #ffffff;
    --edge: #6b6b78;
  }
  * { margin: 0; padding: 0; box-sizing: border-box; }
  html, body { width: 975px; height: 1200px; overflow: hidden; }
  body {
    position: relative;
    background: var(--page);
    font-family: "Open Sans", Arial, sans-serif;
    color: var(--ink);
  }
  .card {
    position: absolute;
    left: 58px;
    width: 860px;
    height: 491px;
    overflow: hidden;
  }
  .card--front { top: 85px; background: var(--white); border: 1px solid var(--edge); }
  .card--back { top: 624px; background: var(--back); }
  .band {
    position: absolute;
    left: 0; right: 0; bottom: 0;
    height: 93px;
    background: var(--navy);
  }
  .wordmark {
    position: absolute;
    font-weight: 700;
    color: var(--navy);
    line-height: 1;
    letter-spacing: -1px;
  }
  .card--front .wordmark { left: 50px; top: 28px; font-size: 100px; }
  .card--back .wordmark { left: 0; right: 0; top: 110px; text-align: center; font-size: 200px; letter-spacing: -3px; }
  .holder {
    position: absolute;
    left: 90px; width: 198px;
    top: 193px;
    text-align: center;
  }
  .holder__name { font-size: 28px; font-weight: 700; line-height: 1.2; }
  .holder__role { font-size: 24px; font-weight: 400; line-height: 1.3; }
  .ribbon { position: absolute; left: 0; top: 0; }
  .contact {
    position: absolute;
    left: 502px;
    font-size: 21px;
    color: var(--navy);
    line-height: 1.35;
  }
  .contact--phone { top: 62px; }
  .contact--email { top: 124px; }
  .contact--web { top: 185px; letter-spacing: 2px; }
  .contact--address { top: 245px; }
  .back-web {
    position: absolute;
    left: 0; right: 0; bottom: 0;
    height: 93px;
    line-height: 93px;
    text-align: center;
    color: var(--white);
    font-size: 26px;
    letter-spacing: 3px;
  }
</style>
</head>
<body>
  <section class="card card--front">
    <div class="wordmark">pexla</div>
    <div class="holder">
      <p class="holder__name">JOHN SMITH</p>
      <p class="holder__role">Position</p>
    </div>

    <svg class="ribbon" width="860" height="491" viewBox="0 0 860 491" aria-hidden="true">
      <polygon points="423,0 451,0 451,382 437,352 423,382" fill="var(--navy)"/>
      <g fill="none" stroke="var(--ink)" stroke-width="1.8">
        <!-- tabs -->
        <g transform="translate(391,41)">
          <polygon points="0,47 86,47 64,62 22,62" fill="var(--tab-fold)" stroke="none"/>
          <rect width="86" height="47" fill="var(--tab)" stroke="none"/>
          <circle cx="43" cy="23" r="10"/>
          <path d="M38.5 17.5 l2.5 0 1.2 3 -1.6 1.4 c0.8 1.8 2 3 3.8 3.8 l1.4 -1.6 3 1.2 0 2.5 c-6 0.5 -10.8 -4.3 -10.3 -10.3z" fill="var(--ink)" stroke="none"/>
        </g>
        <g transform="translate(391,103)">
          <polygon points="0,47 86,47 64,62 22,62" fill="var(--tab-fold)" stroke="none"/>
          <rect width="86" height="47" fill="var(--tab)" stroke="none"/>
          <rect x="33" y="16" width="20" height="14" fill="var(--ink)" stroke="none"/>
          <path d="M33 16 l10 8 10 -8 M33 30 l7 -7 M53 30 l-7 -7" stroke="var(--tab)" stroke-width="1.4"/>
        </g>
        <g transform="translate(391,165)">
          <polygon points="0,47 86,47 64,62 22,62" fill="var(--tab-fold)" stroke="none"/>
          <rect width="86" height="47" fill="var(--tab)" stroke="none"/>
          <circle cx="43" cy="25" r="9.5"/>
          <ellipse cx="43" cy="25" rx="4" ry="9.5"/>
          <path d="M33.5 25 h19 M35 20 h16 M35 30 h16"/>
        </g>
        <g transform="translate(393,227)">
          <polygon points="0,47 86,47 64,62 22,62" fill="var(--tab-fold)" stroke="none"/>
          <rect width="86" height="47" fill="var(--tab)" stroke="none"/>
          <circle cx="43" cy="24" r="10.5"/>
          <path d="M43 31 c-3 -4 -5 -6.5 -5 -9 a5 5 0 0 1 10 0 c0 2.5 -2 5 -5 9z"/>
          <circle cx="43" cy="22" r="1.6" fill="var(--ink)" stroke="none"/>
        </g>
      </g>
    </svg>

    <p class="contact contact--phone">012-345-6789</p>
    <p class="contact contact--email">info@pexla.com</p>
    <p class="contact contact--web">www.pexla.com</p>
    <p class="contact contact--address">Street name City Name,<br>Zipcode,012345</p>

    <div class="band"></div>
  </section>

  <section class="card card--back">
    <div class="wordmark">pexla</div>
    <div class="band"></div>
    <p class="back-web">www.pexla.com</p>
  </section>
</body>
</html>
```